KBT Business Cards

We require business cards for our business. We would like a matte black back to the card, with our logo centred in the middle. The front side of the card is open to design.

Target Market(s)

Clients looking for legal services (professional)

Industry/Entity Type

Legal

Contact Information for Business Card

Doran Kelbrath
Partner
Mobile: 0461 738 524
Email: doran@kbtlaw.co
Website: www.kbtlaw.co
Level 3, 118 Wendmore Street
Sydney NSW 2000

Font styles to use
Other font styles liked:
• Avenir

Colors
f04a50
ffffff
1b1b1b

Requirements
Must have
• Black back with logo included in the centre of the card.
• Our font is Avenir.

```html
<!DOCTYPE html>
<html lang="en">
<head>
<meta charset="utf-8">
<title>KBT Legal – Business Card</title>
<link rel="stylesheet" href="https://fonts.googleapis.com/css2?family=Nunito+Sans:wght@300;400;700;800&display=swap">
<style>
  :root {
    --brand-red: #8e1f2e;
    --accent-red: #f04a50;
    --ink: #1b1b1b;
    --paper: #ffffff;
    --card-light: #eef0f2;
    --stage: #d9d6d2;
    --contact-text: #c8b9a6;
    --icon-ring: #d8c8b4;
  }
  * { box-sizing: border-box; margin: 0; padding: 0; }
  html, body { width: 1200px; height: 970px; overflow: hidden; }
  body {
    background: var(--stage);
    font-family: "Nunito Sans", sans-serif;
    position: relative;
  }
  .card {
    position: absolute;
    left: 100px; top: 199px;
    width: 1000px; height: 572px;
    border-radius: 32px;
    overflow: hidden;
    background: linear-gradient(160deg, var(--paper) 0%, var(--card-light) 100%);
    box-shadow: 0 18px 40px rgba(0,0,0,0.25);
  }
  .card-artwork {
    position: absolute;
    left: 0; top: 0;
    width: 1000px; height: 572px;
    background: linear-gradient(100deg, #5a1822 0%, #2a1517 30%, var(--ink) 55%, #080808 100%);
    clip-path: polygon(0 78%, 100% 44%, 100% 100%, 0 100%);
  }
  .firm-name {
    position: absolute;
    left: 60px; top: 108px;
    display: flex; align-items: center; gap: 48px;
  }
  .firm-mark { width: 150px; height: 150px; background: var(--brand-red); }
  .firm-wordmark {
    font-weight: 800;
    font-size: 46px;
    line-height: 1.0;
    color: var(--ink);
    letter-spacing: 0.3px;
  }
  .person {
    position: absolute;
    right: 50px; top: 74px;
    text-align: right;
  }
  .person-name {
    font-weight: 800;
    font-size: 29px;
    color: var(--brand-red);
    letter-spacing: 0.3px;
    line-height: 1.05;
  }
  .person-title {
    font-weight: 400;
    font-size: 24px;
    color: var(--ink);
    line-height: 1.05;
  }
  .contacts {
    position: absolute;
    right: 50px; top: 338px;
    list-style: none;
  }
  .contact-item {
    display: flex; justify-content: flex-end; align-items: center;
    gap: 18px;
    height: 37px;
    font-weight: 300;
    font-size: 24px;
    color: var(--contact-text);
    letter-spacing: 0.4px;
  }
  .contact-icon { width: 32px; height: 32px; }
  .address {
    position: absolute;
    right: 50px; top: 460px;
    text-align: right;
    font-style: normal;
    font-weight: 300;
    font-size: 24px;
    line-height: 37px;
    color: var(--contact-text);
    letter-spacing: 0.4px;
  }
</style>
</head>
<body>
  <section class="card" aria-label="KBT Legal business card, front">
    <div class="card-artwork" role="img" aria-label="Decorative red and black wave artwork across the lower card"></div>

    <div class="firm-name">
      <span class="firm-mark"></span>
      <span class="firm-wordmark">KBT<br>LEGAL</span>
    </div>

    <div class="person">
      <p class="person-name">DORAN KELBRATH</p>
      <p class="person-title">Partner</p>
    </div>

    <ul class="contacts">
      <li class="contact-item">0461 738 524
        <svg class="contact-icon" viewBox="0 0 30 30" aria-hidden="true">
          <circle cx="15" cy="15" r="13" fill="none" stroke="var(--icon-ring)" stroke-width="2.5"/>
          <rect x="10" y="8" width="10" height="14" rx="2" fill="none" stroke="var(--icon-ring)" stroke-width="2"/>
        </svg>
      </li>
      <li class="contact-item">doran@kbtlaw.co
        <svg class="contact-icon" viewBox="0 0 30 30" aria-hidden="true">
          <circle cx="15" cy="15" r="13" fill="none" stroke="var(--icon-ring)" stroke-width="2.5"/>
          <rect x="8" y="10" width="14" height="10" fill="none" stroke="var(--icon-ring)" stroke-width="1.8"/>
          <path d="M8,10 L15,16 L22,10" fill="none" stroke="var(--icon-ring)" stroke-width="1.8"/>
        </svg>
      </li>
      <li class="contact-item">www.kbtlaw.co
        <svg class="contact-icon" viewBox="0 0 30 30" aria-hidden="true">
          <circle cx="15" cy="15" r="13" fill="none" stroke="var(--icon-ring)" stroke-width="2.5"/>
          <circle cx="15" cy="15" r="7.5" fill="none" stroke="var(--icon-ring)" stroke-width="1.6"/>
          <ellipse cx="15" cy="15" rx="3.5" ry="7.5" fill="none" stroke="var(--icon-ring)" stroke-width="1.4"/>
          <line x1="7.5" y1="15" x2="22.5" y2="15" stroke="var(--icon-ring)" stroke-width="1.4"/>
        </svg>
      </li>
    </ul>

    <address class="address">
      Level 3, 118 Wendmore Street<br>
      Sydney NSW 2000
    </address>
  </section>
</body>
</html>
```